first fantastic look and impression

We are looking for a concept for letterhead, business card, emailfooter and template for invoices or offers for our company in the consultation business.
The dancer is a symbol who we are: it looks simple, but there is a lot of hard work and many years of training in this movement. The look is also what we want: elegant, modern, strong, with a touch of extravaganza
Target Market(s)
Hotelbusiness , Consulting
Font styles to use
Sans Serif
Other font styles liked:
- please give us a option we are open
Requirements
Must have
- We are not typical consultants but sparring partners and coaches for the hotel and that should also be expressed in the design. Maybe there is an icon that supports the whole thing. We are more modern and bolder than our industry colleagues.
we are modern, fresh, agile, fast
Nice to have
- a icon

```html
<!DOCTYPE html>
<html lang="en">
<head>
<meta charset="utf-8">
<title>Kestrel Coaching – Letterhead</title>
<link rel="stylesheet" href="https://fonts.googleapis.com/css2?family=Open+Sans:wght@400;700&display=swap">
<style>
  :root {
    --backdrop: #d6dbde;
    --paper: #ffffff;
    --slate-blue: #6b8aa8;
    --ink-blue: #4d6f93;
    --ink-grey: #5a5f66;
    --gold: #e3c27c;
    --gold-light: #efd9a6;
    --hairline: #b9c3cc;
    --figure-light: #f3f4f6;
    --figure-mid: #e4e6ea;
  }
  * { margin: 0; padding: 0; box-sizing: border-box; }
  html, body {
    width: 1200px; height: 784px; overflow: hidden;
    background: var(--backdrop);
  }
  .letterhead {
    position: absolute;
    left: 340px; top: 24px;
    width: 520px; height: 736px;
    background: var(--paper);
    box-shadow: 0 4px 18px rgba(60, 70, 80, 0.18);
    overflow: hidden;
  }
  .corner-accent { position: absolute; left: 0; top: 0; }
  .brand-name {
    position: absolute;
    left: 30px; top: 58px;
    font-family: "Open Sans", Arial, sans-serif;
    font-weight: 400;
    font-size: 19px;
    letter-spacing: 0.4px;
    color: var(--ink-blue);
  }
  .hero-figure {
    position: absolute;
    left: 110px; top: 210px;
    width: 260px; height: 200px;
    border-radius: 48% 52% 40% 60% / 55% 45% 55% 45%;
    background: radial-gradient(ellipse at 45% 45%, var(--figure-mid) 0%, var(--figure-light) 55%, rgba(255,255,255,0) 78%);
  }
  .contact {
    position: absolute;
    left: 370px; top: 54px;
    font-family: "Open Sans", Arial, sans-serif;
    font-style: normal;
    font-weight: 400;
    font-size: 8.5px;
    line-height: 13px;
    color: var(--ink-grey);
  }
  .contact-rule {
    position: absolute;
    left: -38px; top: -6px;
  }
  .contact-item { display: flex; align-items: center; gap: 4px; }
  .contact-item svg { flex: none; }
  .contact-city { font-weight: 700; color: var(--ink-blue); }
</style>
</head>
<body>
  <main class="letterhead">
    <svg class="corner-accent" width="520" height="736" viewBox="0 0 520 736" aria-hidden="true">
      <polygon points="0,0 205,0 0,46" fill="var(--slate-blue)"/>
      <polygon points="285,736 520,736 520,698" fill="var(--gold)"/>
      <polygon points="285,736 400,736 520,716 520,698" fill="var(--gold-light)" opacity="0.6"/>
    </svg>

    <div class="brand-name">Kestrel Coaching</div>

    <div class="hero-figure" role="img" aria-label="Faint photograph of a dancer in a flowing dress, mid-movement"></div>

    <address class="contact">
      <svg class="contact-rule" width="36" height="44" viewBox="0 0 36 44" aria-hidden="true">
        <line x1="34" y1="0" x2="2" y2="44" stroke="var(--hairline)" stroke-width="0.8"/>
      </svg>
      <div class="contact-item contact-city">
        <svg width="8" height="8" viewBox="0 0 8 8" aria-hidden="true"><circle cx="4" cy="4" r="3.6" fill="none" stroke="var(--ink-blue)" stroke-width="0.8"/><circle cx="4" cy="3.5" r="1.2" fill="var(--ink-blue)"/></svg>
        Kirchwald/Austria
      </div>
      <div class="contact-item">
        <svg width="8" height="8" viewBox="0 0 8 8" aria-hidden="true"><rect x="0.5" y="1.5" width="7" height="5" rx="0.6" fill="var(--ink-blue)"/><polyline points="0.8,2 4,4.5 7.2,2" fill="none" stroke="#fff" stroke-width="0.6"/></svg>
        hello@kestrelcoaching.com
      </div>
      <div class="contact-item">
        <svg width="8" height="8" viewBox="0 0 8 8" aria-hidden="true"><circle cx="4" cy="4" r="3.6" fill="none" stroke="var(--ink-blue)" stroke-width="0.8"/><circle cx="4" cy="4" r="1.8" fill="none" stroke="var(--ink-blue)" stroke-width="0.6"/></svg>
        kestrelcoaching.com
      </div>
    </address>
  </main>
</body>
</html>
```